Northvale Strategy Partners Website Design

I need a website design for my new business consulting and executive coaching firm, Northvale Strategy Partners. We provide consultative services to business C-suites as well as personal coaching to executives. I have attached the logo with color scheme I have chosen. I would like the website to reflect professionalism and continue the color scheme in the logo.

Target Market(s)

Small to medium business and their executives; middle to upper income men and women in mid- to late career looking for significance

Industry/Entity Type

Business Consultant

Number of Pages Required

4 page

Requirements
Must have
• A homepage with prominent logo and way to contact for more information; an area on the homepage with easy to read, clear text to describe what the company does; a prominent area on the homepage for a tagline; a blog page that can be updated regularly, an "about us" page with biographical information; an "about us" page; a page detailing services offered
• The web design must match the logo colors and font that I have uploaded.
Nice to have
• A lighthouse picture in the background or header
Should not have
• A lot of text area on the homepage

```html
<!DOCTYPE html>
<html lang="en">
<head>
<meta charset="utf-8">
<title>Northvale Strategy Partners</title>
<link href="https://fonts.googleapis.com/css2?family=Raleway:wght@400;500;600;700&family=Lato:wght@400;700&display=swap" rel="stylesheet">
<style>
  :root {
    --maroon: #6c1115;
    --navy: #1f2b57;
    --ink: #222222;
    --body: #2e2e2e;
    --muted: #444444;
    --hero-light: #fbf6f1;
    --hero-warm: #efc9a4;
    --hero-skin: #d99567;
    --section-light: #f1f1f1;
    --section-mid: #dcdcdc;
    --panel: rgba(226,226,226,0.72);
    --fb: #3b5998;
    --gp: #dd4b39;
    --tw: #55acee;
  }
  * { margin: 0; padding: 0; box-sizing: border-box; }
  html, body { width: 1200px; height: 1200px; overflow: hidden; }
  body { position: relative; font-family: "Raleway", sans-serif; color: var(--ink); background: #fff; }

  .hero {
    position: absolute; left: 0; top: 0; width: 1200px; height: 669px;
    background: linear-gradient(100deg, var(--hero-light) 0%, var(--hero-light) 38%, #f6e2cf 55%, var(--hero-warm) 72%, var(--hero-skin) 88%, #c8c4c4 100%);
  }
  .hero-photo {
    position: absolute; left: 560px; top: 130px; width: 640px; height: 539px;
    background: radial-gradient(ellipse at 60% 40%, rgba(217,149,103,0.55), rgba(239,201,164,0.2) 55%, rgba(255,255,255,0) 75%);
  }

  .brand {
    position: absolute; left: 160px; top: 44px; display: flex; align-items: center; gap: 8px;
    font-weight: 700; font-size: 17px; color: var(--navy); line-height: 1.1; width: 170px;
  }
  .brand-mark { width: 14px; height: 14px; background: var(--maroon); flex: none; }

  .contact-line {
    position: absolute; right: 270px; top: 22px; font-size: 10.5px; color: var(--ink);
  }
  .contact-line strong { font-weight: 700; color: var(--navy); }
  .social { position: absolute; left: 952px; top: 15px; display: flex; gap: 4px; }
  .social span { width: 26px; height: 26px; border-radius: 6px; display: block; }
  .social .s1 { background: var(--fb); }
  .social .s2 { background: var(--gp); }
  .social .s3 { background: var(--tw); }

  .main-nav {
    position: absolute; right: 162px; top: 64px; display: flex; gap: 18px;
    font-size: 12.5px; font-weight: 700; letter-spacing: 0.1px;
  }
  .main-nav a { color: var(--ink); text-decoration: none; padding-bottom: 2px; }
  .main-nav a.active { color: var(--maroon); border-bottom: 2px solid var(--maroon); }

  .hero-title { position: absolute; left: 158px; top: 258px; color: var(--maroon); }
  .hero-title h1 { font-size: 43px; font-weight: 700; line-height: 1.1; }
  .hero-title h2 { font-size: 27px; font-weight: 600; line-height: 1.1; margin-top: 0; }
  .hero-copy { position: absolute; left: 159px; top: 354px; width: 350px; font-size: 12px; line-height: 16px; color: var(--body); letter-spacing: 0.2px; }
  .hero-copy p + p { margin-top: 16px; }
  .read-more {
    position: absolute; left: 554px; top: 604px; width: 98px; height: 35px;
    border: 2px solid var(--navy); color: var(--navy); font-size: 10.5px; font-weight: 700;
    display: flex; align-items: center; justify-content: center; letter-spacing: 0.4px;
  }
  .arrow { position: absolute; top: 320px; }
  .arrow.prev { left: 30px; }
  .arrow.next { left: 1152px; }

  .intro {
    position: absolute; left: 0; top: 669px; width: 1200px; height: 531px;
    background: linear-gradient(90deg, var(--section-mid) 0%, var(--section-light) 45%, #f4f4f4 100%);
  }
  .intro-photo {
    position: absolute; left: 70px; top: 10px; width: 540px; height: 521px;
    background: radial-gradient(ellipse at 55% 55%, #fafafa 0%, #e3e3e3 55%, rgba(220,220,220,0) 80%);
  }
  .intro-title { position: absolute; left: 611px; top: 50px; width: 420px; color: var(--maroon); font-size: 30px; font-weight: 700; line-height: 32.5px; }
  .intro-copy { position: absolute; left: 611px; top: 193px; width: 455px; font-size: 12.5px; line-height: 16px; color: var(--body); }
  .intro-copy p + p { margin-top: 15px; }

  .services {
    position: absolute; left: 150px; top: 1005px; width: 900px; height: 195px;
    background: var(--panel);
  }
  .service { position: absolute; width: 290px; height: 120px; }
  .service svg { position: absolute; left: 0; top: 0; }
  .service h3 { position: absolute; left: 75px; top: 18px; font-family: "Raleway", sans-serif; font-size: 13.6px; font-weight: 600; color: var(--ink); }
  .service p { position: absolute; left: 76px; top: 48px; width: 205px; font-family: "Lato", sans-serif; font-size: 9.6px; line-height: 13.6px; color: var(--muted); }
</style>
</head>
<body>

<section class="hero">
  <div class="hero-photo" role="img" aria-label="Close-up of a hand typing on a white keyboard in warm light"></div>

  <div class="brand"><span class="brand-mark"></span><span>Northvale Strategy Partners</span></div>

  <div class="contact-line">Call Us: <strong>555.014.2290</strong> &nbsp;/&nbsp; Email Us: <strong>hello@northvalestrategy.com</strong></div>
  <div class="social" aria-label="Social links"><span class="s1"></span><span class="s2"></span><span class="s3"></span></div>

  <nav class="main-nav">
    <a class="active" href="#">HOME</a>
    <a href="#">ABOUT US</a>
    <a href="#">SERVICES</a>
    <a href="#">SUCCESS STORIES</a>
    <a href="#">BLOG</a>
    <a href="#">CONTACT US</a>
  </nav>

  <svg class="arrow prev" width="20" height="30" viewBox="0 0 20 30"><path d="M15 4 L5 15 L15 26" fill="none" stroke="#fff" stroke-width="2.5"/></svg>
  <svg class="arrow next" width="20" height="30" viewBox="0 0 20 30"><path d="M5 4 L15 15 L5 26" fill="none" stroke="#fff" stroke-width="2.5"/></svg>

  <div class="hero-title">
    <h1>Business Consulting &amp;</h1>
    <h2>Executive Coaching Firm</h2>
  </div>
  <div class="hero-copy">
    <p>Lorem ipsum dolor sit amet, consectetur adipisicing elit, sed do eiusmod tempor incididunt ut labore et dolore magna aliqua.</p>
    <p>Ut enim ad minim veniam, quis nostrud exercitation ullamco laboris nisi ut aliquip ex ea commodo consequat.</p>
  </div>
  <div class="read-more">READ MORE</div>
</section>

<section class="intro">
  <div class="intro-photo" role="img" aria-label="Thoughtful businessman in a white shirt holding a pen at his desk"></div>
  <h2 class="intro-title">Attackers employ new methods every day.<br>It is time for you to step up your game.</h2>
  <div class="intro-copy">
    <p>Lorem ipsum dolor sit amet, consectetur adipisicing elit, sed do eiusmod tempor incididunt ut labore et dolore magna aliqua. Ut enim ad minim veniam, quis nostrud exercitation ullamco laboris nisi ut aliquip ex ea commodo consequat.</p>
    <p>Duis aute irure dolor in reprehenderit in voluptate velit esse cillum dolore eu fugiat nulla pariatur. Excepteur sint occaecat cupidatat non proident, sunt in culpa qui officia deserunt mollit anim id est laborum.</p>
  </div>
</section>

<section class="services">
  <div class="service" style="left:10px; top:8px;">
    <svg width="60" height="60" viewBox="0 0 60 60">
      <circle cx="25" cy="15" r="9" fill="var(--navy)"/>
      <path d="M6 52 C6 36 14 28 25 28 C36 28 44 36 44 52 Z" fill="var(--navy)"/>
      <circle cx="44" cy="46" r="9" fill="var(--navy)" stroke="#e6e6e6" stroke-width="2"/>
      <circle cx="43" cy="45" r="3.5" fill="none" stroke="#fff" stroke-width="1.6"/>
      <line x1="45.5" y1="47.5" x2="48.5" y2="50.5" stroke="#fff" stroke-width="1.6"/>
    </svg>
    <h3>Consultative Services</h3>
    <p>Nam vel eleifend que fusce consequat pretium velit vitae. Vulputate nullam pharetra lorem laoreet. Etiam sollicitudin magna nullam.</p>
  </div>
  <div class="service" style="left:310px; top:8px;">
    <svg width="60" height="60" viewBox="0 0 60 60">
      <path d="M14 44 H46 A9 9 0 0 0 45 26 A12 12 0 0 0 23 22 A9 9 0 0 0 14 44 Z" fill="none" stroke="var(--navy)" stroke-width="2.6" stroke-linejoin="round"/>
    </svg>
    <h3>Executive Coaching</h3>
    <p>Nam vel eleifend que fusce consequat pretium velit vitae. Vulputate nullam pharetra lorem laoreet. Etiam sollicitudin magna nullam.</p>
  </div>
  <div class="service" style="left:610px; top:8px;">
    <svg width="60" height="60" viewBox="0 0 60 60">
      <path d="M30 5 C19 5 13 13 13 21 C13 29 21 33 22 42 H38 C39 33 47 29 47 21 C47 13 41 5 30 5 Z" fill="none" stroke="var(--navy)" stroke-width="2.6"/>
      <line x1="23" y1="47" x2="37" y2="47" stroke="var(--navy)" stroke-width="2.6"/>
      <line x1="25" y1="52" x2="35" y2="52" stroke="var(--navy)" stroke-width="2.6"/>
      <path d="M27 42 V30 H33 V42" fill="none" stroke="var(--navy)" stroke-width="1.6"/>
    </svg>
    <h3>Fresh &amp; Right Ideas</h3>
    <p>Nam vel eleifend que fusce consequat pretium velit vitae. Vulputate nullam pharetra lorem laoreet. Etiam sollicitudin magna nullam.</p>
  </div>
  <div class="service" style="left:10px; top:137px;">
    <svg width="60" height="60" viewBox="0 0 60 60">
      <circle cx="28" cy="16" r="9" fill="var(--navy)"/>
      <path d="M12 52 C12 36 18 28 28 28 C38 28 44 36 44 52 Z" fill="var(--navy)"/>
      <rect x="16" y="38" width="24" height="14" fill="#fff" stroke="var(--navy)" stroke-width="2"/>
      <line x1="28" y1="38" x2="28" y2="52" stroke="var(--navy)" stroke-width="1.5"/>
    </svg>
    <h3>Personal Coaching</h3>
    <p>Nam vel eleifend que fusce consequat pretium velit vitae.</p>
  </div>
  <div class="service" style="left:310px; top:137px;">
    <svg width="60" height="60" viewBox="0 0 60 60">
      <rect x="3" y="15" width="38" height="32" rx="4" fill="none" stroke="var(--navy)" stroke-width="3"/>
      <rect x="11" y="22" width="22" height="18" fill="var(--navy)"/>
      <path d="M41 27 L54 18 V44 L41 35 Z" fill="none" stroke="var(--navy)" stroke-width="3" stroke-linejoin="round"/>
    </svg>
    <h3>Business Consulting</h3>
    <p>Nam vel eleifend que fusce consequat pretium velit vitae.</p>
  </div>
</section>

</body>
</html>
```